business card deign

Logo needs the following on it.
1. attached logo
2. Tagline - "If it keeps a drink cold or the party going...we do it!"
3. Name- Dalton Pikes, Founder and CPO
4. Address - 412 E. Carver Avenue, Ste 2207, Tampa, FL. 33917
5. Phone - 555.318.4726

```html
<!DOCTYPE html>
<html lang="en">
<head>
<meta charset="utf-8">
<title>Kelvora Business Card</title>
<link rel="stylesheet" href="https://fonts.googleapis.com/css2?family=Montserrat:wght@400;700&display=swap">
<style>
  :root {
    --stage: #161616;
    --card: #262626;
    --card-edge: #2e2e2e;
    --ink: #ffffff;
    --ink-soft: #e6e6e6;
    --pattern-dark: #1e1e1e;
    --pattern-light: #5a5a5a;
  }
  * { box-sizing: border-box; margin: 0; padding: 0; }
  html, body {
    width: 1200px; height: 900px; overflow: hidden;
    background: var(--stage);
    font-family: "Montserrat", Arial, sans-serif;
    color: var(--ink);
  }
  .stage {
    width: 1200px; height: 900px;
    display: flex; flex-direction: column; align-items: center; justify-content: center; gap: 40px;
  }
  .card {
    position: relative;
    width: 700px; height: 400px;
    border-radius: 22px;
    background: var(--card);
    box-shadow: 0 0 0 1px var(--card-edge);
    overflow: hidden;
  }
  .brand {
    display: flex; align-items: center; gap: 14px;
    font-weight: 700; letter-spacing: 0.42em; text-transform: uppercase;
  }
  .brand-dot {
    width: 18px; height: 18px; border-radius: 50%; background: var(--ink);
  }

  /* Front */
  .card-front .brand {
    position: absolute; top: 82px; left: 0; right: 0; justify-content: center;
    font-size: 34px;
  }
  .contact-row {
    position: absolute; top: 190px; left: 70px; right: 60px;
    display: flex; align-items: center;
  }
  .person { text-align: right; padding-right: 24px; }
  .person-name { font-weight: 700; font-size: 25px; letter-spacing: 0.02em; text-transform: uppercase; }
  .person-title { font-size: 17px; margin-top: 4px; color: var(--ink-soft); }
  .divider { width: 1.5px; height: 66px; background: var(--ink); }
  .channels { padding-left: 24px; font-size: 17px; list-style: none; }
  .channels li { display: flex; align-items: center; gap: 10px; line-height: 1.7; }
  .channels svg { width: 15px; height: 15px; fill: var(--ink); }
  .address {
    position: absolute; top: 300px; left: 0; right: 0; text-align: center;
    font-size: 17px; color: var(--ink-soft);
  }

  /* Back */
  .pattern-field {
    position: absolute; inset: 0;
    background: linear-gradient(120deg, var(--pattern-dark) 0%, var(--pattern-dark) 35%, var(--pattern-light) 100%);
    opacity: 0.55;
  }
  .card-back .back-content {
    position: absolute; top: 140px; left: 0; right: 0;
    display: flex; flex-direction: column; align-items: center; gap: 30px;
  }
  .card-back .brand { font-size: 32px; }
  .tagline { font-size: 18px; letter-spacing: 0.01em; }
</style>
</head>
<body>
<main class="stage">
  <section class="card card-front" aria-label="Card front">
    <div class="brand"><span class="brand-dot"></span>Kelvora</div>
    <div class="contact-row">
      <div class="person">
        <p class="person-name">Dalton Pikes</p>
        <p class="person-title">Founder and CPO</p>
      </div>
      <span class="divider"></span>
      <ul class="channels">
        <li>
          <svg viewBox="0 0 24 24" aria-hidden="true"><path d="M6.6 10.8a15 15 0 0 0 6.6 6.6l2.2-2.2c.3-.3.7-.4 1-.2 1.1.4 2.3.6 3.6.6.6 0 1 .4 1 1V20c0 .6-.4 1-1 1C10.6 21 3 13.4 3 4c0-.6.4-1 1-1h3.5c.6 0 1 .4 1 1 0 1.3.2 2.5.6 3.6.1.3 0 .7-.2 1z"/></svg>
          555.318.4726
        </li>
        <li>
          <svg viewBox="0 0 24 24" aria-hidden="true"><path d="M3 5h18v14H3zM4.5 6.5l7.5 6 7.5-6v-.1h-15z"/></svg>
          dalton@kelvora.co
        </li>
      </ul>
    </div>
    <p class="address">412 E. Carver Avenue, Ste 2207, Tampa, FL. 33917</p>
  </section>

  <section class="card card-back" aria-label="Card back">
    <div class="pattern-field" role="img" aria-label="Repeating tonal pattern of the brand symbol across the card"></div>
    <div class="back-content">
      <div class="brand"><span class="brand-dot"></span>Kelvora</div>
      <p class="tagline">If it keeps a drink cold or the party going...we do it!</p>
    </div>
  </section>
</main>
</body>
</html>
```